Business Card: RW Office Partners - Your organised problem solver

Business Name: RW Office Partners
Website: www.rwofficepartners.com.au
Email: marisol@rwofficepartners.com.au
Mobile: 61 482 907 236
Facebook: @rwofficepartners
Instrgram: @rwofficepartners

Brading Colours:
HEX
#986474
#ddccd3
#7a8498
#c9d8e4
#000000
#ffffff

Tag Line: Your dependable task partner

Link to DRAFT website:
https://deskhelpcollective.wixsite.com/rw-office-partners

About Page from the website:
My name is Marisol Wrenfield, and I would love to assist you to become more productive in your day to day and achieve your business and personal goals.
My mission is to give you time, time to work on the important tasks of your business or to be able to spend more time with your family. I will take on the tasks you don’t have time for, don’t know well or simply don’t like to do.
I have an extensive background in Administration, Tender Coordination, Document Control, WHS and Quality Management working primarily in the Construction, Mining and Corporate World.
I am passionate about being organised, having order and making things in your life (and mine) easier! I love to watch something unfold and grow into something amazing! I am known for being the go-to problem solver, the organiser of all things, producing high standards of work even under pressure. I’m also a confident communicator, and I understand that you’re busy running your business.

Target Market(s)

Small to Medium Business who require assistance in their business by a virtual assistant.

Industry/Entity Type

Virtual Assistant

Contact Information for Business Card

Mobile: 61 482 907 236

Font styles to use
Sans Serif

Colors
ffffff

Requirements
Must have
• Branding Colours as outlined.
Contact Details as outlined.
Logo as provided.
Proper contact details - mobile, facebook, instragm, website.
Simple, Elegant, very clean looking.
Should not have
• Note cute with pictures.
Not too girly as still want to market to construction companies.

```html
<!DOCTYPE html>
<html lang="en">
<head>
<meta charset="utf-8">
<title>RW Office Partners – Business Card</title>
<link rel="stylesheet" href="https://fonts.googleapis.com/css2?family=Montserrat:wght@600&family=Roboto:wght@400&display=swap">
<style>
  :root {
    --stage: #2b2b2d;
    --card: #1f1f20;
    --rose: #986474;
    --rose-light: #b07c8c;
    --slate-light: #a3acbe;
    --emboss: #3a3a3d;
  }
  * { margin: 0; padding: 0; box-sizing: border-box; }
  html, body { width: 1200px; height: 900px; overflow: hidden; }
  body {
    background: var(--stage);
    display: flex;
    flex-direction: column;
    align-items: center;
    justify-content: center;
    gap: 48px;
  }
  .card {
    width: 660px;
    height: 378px;
    background: var(--card);
    position: relative;
  }
  /* Back */
  .card--back {
    display: flex;
    align-items: center;
    justify-content: center;
  }
  .back-name {
    font-family: "Montserrat", sans-serif;
    font-weight: 600;
    font-size: 44px;
    letter-spacing: 1px;
    color: var(--emboss);
    text-transform: uppercase;
    text-align: center;
    line-height: 1.1;
  }
  /* Front */
  .brand {
    position: absolute;
    left: 64px;
    top: 92px;
    display: flex;
    align-items: center;
    gap: 12px;
  }
  .brand-mark {
    width: 16px; height: 16px;
    background: var(--rose);
    flex: none;
  }
  .brand-name {
    font-family: "Montserrat", sans-serif;
    font-weight: 600;
    font-size: 25px;
    line-height: 1.15;
    color: var(--slate-light);
    text-transform: uppercase;
  }
  .contact-block {
    position: absolute;
    left: 300px;
    top: 150px;
    display: flex;
    align-items: stretch;
  }
  .divider {
    width: 1.5px;
    background: var(--rose);
    margin-right: 20px;
  }
  .contact-list {
    list-style: none;
    font-family: "Roboto", sans-serif;
    font-size: 16px;
    color: var(--slate-light);
    padding: 4px 0;
  }
  .contact-list li {
    display: flex;
    align-items: center;
    gap: 9px;
    height: 26px;
    white-space: nowrap;
  }
  .contact-list svg { width: 14px; height: 14px; flex: none; }
  .social-dot {
    width: 12px; height: 12px;
    margin: 0 1px;
    background: var(--rose);
    flex: none;
    border-radius: 2px;
  }
  .tagline {
    position: absolute;
    left: 92px;
    top: 262px;
    font-family: "Roboto", sans-serif;
    font-size: 17px;
    color: var(--rose-light);
  }
</style>
</head>
<body>
  <section class="card card--back" aria-label="Card back">
    <p class="back-name">RW Office<br>Partners</p>
  </section>

  <section class="card card--front" aria-label="Card front">
    <div class="brand">
      <span class="brand-mark"></span>
      <span class="brand-name">RW Office<br>Partners</span>
    </div>
    <div class="contact-block">
      <span class="divider"></span>
      <ul class="contact-list">
        <li>
          <svg viewBox="0 0 24 24" fill="var(--rose)"><path d="M6.6 10.8a15 15 0 0 0 6.6 6.6l2.2-2.2a1 1 0 0 1 1-.25 11.4 11.4 0 0 0 3.6.57 1 1 0 0 1 1 1V20a1 1 0 0 1-1 1A17 17 0 0 1 3 4a1 1 0 0 1 1-1h3.5a1 1 0 0 1 1 1c0 1.25.2 2.45.57 3.6a1 1 0 0 1-.25 1z"/></svg>
          61 482 907 236
        </li>
        <li>
          <svg viewBox="0 0 24 24" fill="var(--rose)"><path d="M2 5h20v14H2z M2 5l10 7 10-7" stroke="var(--card)" stroke-width="1.6"/></svg>
          marisol@rwofficepartners.com.au
        </li>
        <li>
          <svg viewBox="0 0 24 24" fill="none" stroke="var(--rose)" stroke-width="2.2"><circle cx="12" cy="12" r="9"/><path d="M3 12h18M12 3c3 3 3 15 0 18M12 3c-3 3-3 15 0 18"/></svg>
          www.rwofficepartners.com.au
        </li>
        <li>
          <span class="social-dot"></span>
          @rwofficepartners
        </li>
      </ul>
    </div>
    <p class="tagline">Your dependable task partner</p>
  </section>
</body>
</html>
```